Need help in designing new business card utilizing our new logo.

BuildMark Solutions works with Construction Business Owners, Managers & IT Professionals to strengthen software usage and increase user productivity.

Our Construction Accounting and Mobile Field Management Software Clients engage with us in the following areas:

New Software Implementations
Software Re-Implementations
Redesigning Software Usage at the User Level
Project Coordination & Management
Continued Software Support

Old tag line:
Weighing Options - Implementing Solutions

www.buildmark-solutions.example

Ridge 4 is a product, but not needed for a new business card.

```html
<!DOCTYPE html>
<html lang="en">
<head>
<meta charset="utf-8">
<title>BuildMark Solutions – Business Card</title>
<link rel="stylesheet" href="https://fonts.googleapis.com/css2?family=Source+Sans+3:wght@400;600;700&display=swap">
<style>
  :root {
    --brand-blue: #0d1ab0;
    --brand-blue-deep: #0a16a0;
    --ink-grey: #4a4a4a;
    --soft-grey: #b9b9bb;
    --card-white: #ffffff;
    --backdrop: #3a3a3c;
    --white: #ffffff;
  }
  * { box-sizing: border-box; margin: 0; padding: 0; }
  html, body { width: 1200px; height: 960px; overflow: hidden; }
  body {
    background: var(--backdrop);
    font-family: "Source Sans 3", "Segoe UI", sans-serif;
    position: relative;
  }
  .card {
    position: absolute;
    width: 598px;
    height: 342px;
    overflow: hidden;
  }
  /* ---------- Front ---------- */
  .card--front { left: 322px; top: 110px; background: var(--card-white); }
  .front-edge { position: absolute; left: 0; top: 0; width: 16px; height: 342px; }
  .brand-name {
    position: absolute; left: 34px; top: 40px;
    display: flex; align-items: center; gap: 10px;
    color: var(--brand-blue); font-weight: 700; font-size: 30px; letter-spacing: 0.5px;
  }
  .brand-square { width: 22px; height: 22px; background: var(--brand-blue); }
  .specialty {
    position: absolute; left: 34px; top: 112px;
    color: var(--ink-grey); font-size: 14.5px; line-height: 19px; text-transform: uppercase;
  }
  .address {
    position: absolute; left: 34px; top: 190px;
    color: var(--ink-grey); font-size: 15px; line-height: 20px;
  }
  .contacts {
    position: absolute; left: 34px; top: 238px; list-style: none;
    color: var(--ink-grey); font-size: 15px; line-height: 19px;
  }
  .contacts li { display: flex; align-items: center; gap: 8px; }
  .contacts svg { width: 14px; height: 14px; fill: var(--brand-blue); flex: none; }
  .person {
    position: absolute; right: 32px; top: 222px; text-align: right; text-transform: uppercase;
  }
  .person-name { color: var(--brand-blue); font-weight: 700; font-size: 20px; letter-spacing: 0.5px; line-height: 22px; }
  .person-role { color: var(--soft-grey); font-weight: 700; font-size: 16px; letter-spacing: 1px; line-height: 18px; }

  /* ---------- Back ---------- */
  .card--back { left: 320px; top: 493px; background: var(--brand-blue); color: var(--white); }
  .back-brand {
    position: absolute; left: 50px; top: 140px;
    display: flex; align-items: center; gap: 10px;
    font-weight: 700; font-size: 24px; color: var(--white);
  }
  .back-brand .brand-square { background: var(--white); }
  .services { position: absolute; left: 236px; top: 78px; }
  .services-intro {
    font-weight: 700; font-size: 14.5px; line-height: 19px; text-transform: uppercase;
  }
  .services-list { list-style: none; font-size: 15px; line-height: 19px; }
  .services-list li::before { content: "\2022\00a0"; }
  .tagline {
    position: absolute; left: 0; right: 0; top: 296px; text-align: center;
    font-size: 15px; text-transform: uppercase;
  }
</style>
</head>
<body>
  <section class="card card--front" aria-label="Business card front">
    <svg class="front-edge" viewBox="0 0 16 342" aria-hidden="true">
      <rect x="0" y="0" width="14" height="160" fill="var(--soft-grey)"/>
      <polygon points="0,156 14,164 14,342 0,342" fill="var(--brand-blue)"/>
    </svg>
    <div class="brand-name"><span class="brand-square"></span>BuildMark Solutions</div>
    <p class="specialty">Construction Accounting<br>Software Consultants</p>
    <p class="address">48b harbor lane-PMB417<br>glenwood falls NY 12999</p>
    <ul class="contacts">
      <li><svg viewBox="0 0 14 14"><path d="M1 4c0-2 3-3 6-3s6 1 6 3v1h-3V4H4v1H1z M3 6h8l1 7H2z"/></svg>866-555-0142ext.100</li>
      <li><svg viewBox="0 0 14 14"><path d="M4 0h6a1 1 0 0 1 1 1v12a1 1 0 0 1-1 1H4a1 1 0 0 1-1-1V1a1 1 0 0 1 1-1zm1 2v9h4V2z"/></svg>518-555-0193</li>
      <li><svg viewBox="0 0 14 14"><path d="M1 3h12v1L7 8 1 4z M1 5.5l6 4 6-4V11H1z"/></svg>dana.whitfield@buildmark-solutions.example</li>
      <li><svg viewBox="0 0 14 14"><circle cx="7" cy="7" r="6"/></svg>www.buildmark-solutions.example</li>
    </ul>
    <div class="person">
      <p class="person-name">Dana R. Whitfield</p>
      <p class="person-role">Owner</p>
    </div>
  </section>

  <section class="card card--back" aria-label="Business card back">
    <div class="back-brand"><span class="brand-square"></span>BuildMark</div>
    <div class="services">
      <p class="services-intro">Our construction accounting<br>and mobile field management<br>software clients engage with us<br>in the following areas:</p>
      <ul class="services-list">
        <li>New Software Implementations</li>
        <li>Software Re-Implementations</li>
        <li>Redesigning Software Usage at the User Level</li>
        <li>Project Coordination &amp; Management</li>
        <li>Continued Software Support</li>
      </ul>
    </div>
    <p class="tagline">Weighing Options - Implementing Solutions</p>
  </section>
</body>
</html>
```